TA BRAMLEY BUSINESS CARD DESIGN PROJECT

We need to utilize our logo that was expertly created on PixelHarbor and now need to match this with a business card design.

```html
<!DOCTYPE html>
<html lang="en">
<head>
<meta charset="utf-8">
<title>TA Bramley Business Card</title>
<link rel="stylesheet" href="https://fonts.googleapis.com/css2?family=Montserrat:wght@500;800&family=Open+Sans:wght@400&display=swap">
<style>
  :root {
    --page: #e9e6e1;
    --card-dark: #161616;
    --brand-blue: #0f56ab;
    --ink-light: #ffffff;
    --shadow: rgba(0, 0, 0, 0.28);
  }
  * { margin: 0; padding: 0; box-sizing: border-box; }
  html, body { width: 1200px; height: 900px; overflow: hidden; background: var(--page); }
  .canvas { position: relative; width: 1200px; height: 900px; }
  .card {
    position: absolute; left: 310px; width: 582px; height: 332px;
    border-radius: 26px; overflow: hidden;
    box-shadow: 0 6px 14px var(--shadow);
  }
  .card-front { top: 86px; background: var(--card-dark); }
  .card-back { top: 470px; background: var(--brand-blue); }

  .wordmark {
    font-family: "Montserrat", sans-serif; font-weight: 800;
    letter-spacing: 0.04em; white-space: nowrap;
  }
  .card-front .wordmark {
    position: absolute; left: 22px; top: 52px;
    font-size: 36px; color: var(--brand-blue);
  }
  .card-back .wordmark {
    position: absolute; left: 0; right: 0; top: 130px; text-align: center;
    font-size: 62px; color: var(--ink-light);
  }

  .person { position: absolute; right: 21px; top: 48px; text-align: right; }
  .person-name {
    font-family: "Montserrat", sans-serif; font-weight: 800;
    font-size: 20px; color: var(--brand-blue); letter-spacing: 0.01em;
  }
  .person-role {
    font-family: "Montserrat", sans-serif; font-weight: 500;
    font-size: 15px; color: var(--ink-light); margin-top: 1px;
  }
  .accent-tab {
    position: absolute; right: 0; top: 52px; width: 8px; height: 38px;
    background: var(--brand-blue);
  }

  .contact {
    position: absolute; left: 22px; top: 181px;
    font-family: "Open Sans", sans-serif; font-size: 16px;
    color: var(--ink-light); line-height: 22px;
  }
  .contact-address { margin-bottom: 24px; }
  .contact-line { display: flex; align-items: center; gap: 8px; }
  .contact-line svg { width: 12px; height: 12px; flex: none; }

  .feature-block {
    position: absolute; left: 240px; top: 146px; width: 342px; height: 159px;
    background: var(--brand-blue); border-radius: 60px 0 0 60px;
  }
  .footer-band {
    position: absolute; left: 0; bottom: 0; height: 20px; background: var(--brand-blue);
  }
  .footer-band.left { width: 289px; }
  .footer-band.right { left: 294px; right: 0; }
</style>
</head>
<body>
<div class="canvas">

  <section class="card card-front">
    <div class="wordmark">TA BRAMLEY</div>

    <div class="person">
      <div class="person-name">DANA WHITLOCK</div>
      <div class="person-role">Managing Director</div>
    </div>
    <div class="accent-tab"></div>

    <div class="feature-block"></div>

    <div class="contact">
      <div class="contact-address">Your address,<br>City State, Zip 1234</div>
      <div class="contact-line">
        <svg viewBox="0 0 12 12"><path d="M2.5 1h2l1 2.6-1.3 1a6 6 0 0 0 2.7 2.7l1-1.3L11 7v2a1.5 1.5 0 0 1-1.6 1.5A9 9 0 0 1 1 2.6 1.5 1.5 0 0 1 2.5 1z" fill="#0f56ab"/></svg>
        <span>123 456 789</span>
      </div>
      <div class="contact-line">
        <svg viewBox="0 0 12 12"><rect x="0.5" y="2.5" width="11" height="7.5" rx="1" fill="#0f56ab"/><path d="M1 3l5 3.6L11 3" stroke="#161616" stroke-width="1" fill="none"/></svg>
        <span>info@yourgmail.com</span>
      </div>
      <div class="contact-line">
        <svg viewBox="0 0 12 12"><circle cx="6" cy="6" r="5.2" fill="#0f56ab"/><path d="M1 6h10M6 0.8c-2 2.6-2 7.8 0 10.4M6 0.8c2 2.6 2 7.8 0 10.4" stroke="#161616" stroke-width="0.8" fill="none"/></svg>
        <span>www.yourwebsite.com</span>
      </div>
    </div>

    <div class="footer-band left"></div>
    <div class="footer-band right"></div>
  </section>

  <section class="card card-back">
    <div class="wordmark">TA BRAMLEY</div>
  </section>

</div>
</body>
</html>
```